Business card for a new innovative and professional lawn care business

We need a business card design for a new lawn care business in Halifax NS Canada. We offer lawn services in Halifax & Bedford. Our services offered include lawn care, garden services, and property maintenance. We take pride in our work and are experienced at what we do. I would like to see a design that is double sided. On the backside I would like the something simple (maybe my logo preferably on blackround (linked below) with website link, Facebook page or something). The front I want to include contact info:
Morgan Pell
phone 902-555-0148
email - brookvaleyards.ca
facebook - Facebook.com/brookvaleyards
Instagram maybe ? - instagram.com/brookvaleyard
Serving Halifax and Bedford for 5 years?
I don't want it to have too much information as I will be passing them out in aim to visit website, or call !
We do want it to include lawn care, garden services and property maintenance.
Basic, catchy, and modern looking !
Logo attached below !

Target Market(s)

Passing business cards to everyone I meet or interact with.

Industry/Entity Type

Lawn Care

Contact Information for Business Card

Double sided with some basic information, with catchy colours and easy to look at.

Font styles to use
Sans Serif

Requirements
Must have
• Must be double sided and have :
• Name, Phone, Email, FB, Website, and 3 main services offered - lawn care, property maintenance, garden services
Nice to have
• Would be nice to have instagram link if it goes well on there
Should not have
• Don't want too much writing or images that are distracting

```html
<!DOCTYPE html>
<html lang="en">
<head>
<meta charset="utf-8">
<title>Brookvale Yards – Business Card</title>
<link rel="stylesheet" href="https://fonts.googleapis.com/css2?family=Open+Sans:wght@400;600;700&display=swap">
<style>
  :root {
    --backdrop: #474747;
    --card: #ffffff;
    --leaf-light: #8dc63f;
    --leaf-dark: #006837;
    --ink: #4d4d4d;
    --rule: #d9d9d9;
  }
  * { box-sizing: border-box; margin: 0; padding: 0; }
  html, body {
    width: 1105px; height: 1200px; overflow: hidden;
    background: var(--backdrop);
    font-family: "Open Sans", Arial, sans-serif;
  }
  .canvas { position: relative; width: 1105px; height: 1200px; }
  .card {
    position: absolute; left: 196px; width: 720px; height: 412px;
    background: var(--card); overflow: hidden;
  }
  .card--front { top: 146px; }
  .card--back { top: 602px; }

  /* front */
  .brand {
    position: absolute; left: 62px; top: 150px; width: 300px;
    display: flex; align-items: center; gap: 14px;
  }
  .brand__dot {
    width: 26px; height: 26px; border-radius: 50%;
    background: var(--leaf-light); flex: none;
  }
  .brand__name {
    font-weight: 700; font-size: 38px; line-height: 1.05;
    color: var(--leaf-dark);
  }
  .divider {
    position: absolute; left: 391px; top: 104px; width: 1px; height: 206px;
    background: var(--rule);
  }
  .contact { position: absolute; left: 421px; top: 110px; }
  .contact__name {
    font-weight: 600; font-size: 27px; color: var(--leaf-dark);
    margin-bottom: 14px;
  }
  .contact__list { list-style: none; }
  .contact__item {
    display: flex; align-items: center; gap: 10px;
    font-size: 19px; line-height: 27.6px; color: var(--ink);
  }
  .contact__icon { width: 17px; height: 17px; flex: none; fill: var(--leaf-dark); }
  .band { position: absolute; left: 0; bottom: 0; width: 720px; height: 28px; }

  /* back */
  .back-brand {
    position: absolute; left: 0; right: 0; top: 170px;
    display: flex; justify-content: center; align-items: center; gap: 18px;
  }
  .back-brand__dot {
    width: 40px; height: 40px; border-radius: 50%; background: var(--leaf-light);
  }
  .back-brand__name { font-weight: 700; font-size: 52px; color: var(--leaf-dark); }
  .services {
    position: absolute; left: 0; right: 0; top: 344px;
    display: flex; justify-content: center; align-items: center; gap: 10px;
    font-size: 19px; color: var(--ink);
  }
  .services__sep {
    width: 10px; height: 10px; border-radius: 50%; background: var(--leaf-light);
  }
</style>
</head>
<body>
<main class="canvas">

  <section class="card card--front" aria-label="Card front">
    <div class="brand">
      <span class="brand__dot"></span>
      <span class="brand__name">Brookvale Yards</span>
    </div>
    <div class="divider"></div>
    <div class="contact">
      <h1 class="contact__name">Morgan Pell</h1>
      <ul class="contact__list">
        <li class="contact__item">
          <svg class="contact__icon" viewBox="0 0 24 24" aria-hidden="true"><path d="M6.6 10.8a15.1 15.1 0 0 0 6.6 6.6l2.2-2.2c.3-.3.7-.4 1-.2 1.1.4 2.3.6 3.6.6.6 0 1 .4 1 1V20c0 .6-.4 1-1 1A17 17 0 0 1 3 4c0-.6.4-1 1-1h3.5c.6 0 1 .4 1 1 0 1.3.2 2.5.6 3.6.1.3 0 .7-.2 1z"/></svg>
          902-555-0148
        </li>
        <li class="contact__item">
          <svg class="contact__icon" viewBox="0 0 24 24" aria-hidden="true"><path d="M2 5h20v14H2zm2 2v.4l8 5.2 8-5.2V7zm0 2.8V17h16V9.8l-8 5.2z"/></svg>
          info@brookvaleyards.ca
        </li>
        <li class="contact__item">
          <svg class="contact__icon" viewBox="0 0 24 24" aria-hidden="true"><path d="M12 2a10 10 0 1 0 0 20 10 10 0 0 0 0-20zm0 2c.9 1.2 1.6 2.5 2 4h-4c.4-1.5 1.1-2.8 2-4zM4.3 14a8 8 0 0 1 0-4h3.4a16 16 0 0 0 0 4zm.9 2h3a15 15 0 0 0 1.4 3.6A8 8 0 0 1 5.2 16zm3-8h-3a8 8 0 0 1 4.4-3.6C8.9 5.5 8.5 6.7 8.2 8zM12 20c-.9-1.2-1.6-2.5-2-4h4c-.4 1.5-1.1 2.8-2 4zm2.3-6H9.7a14 14 0 0 1 0-4h4.6a14 14 0 0 1 0 4zm.1 5.6c.6-1.1 1.1-2.3 1.4-3.6h3a8 8 0 0 1-4.4 3.6zm1.9-5.6a16 16 0 0 0 0-4h3.4a8 8 0 0 1 0 4z"/></svg>
          brookvaleyards.ca
        </li>
        <li class="contact__item">
          <svg class="contact__icon" viewBox="0 0 24 24" aria-hidden="true"><rect x="3" y="3" width="18" height="18" rx="2"/></svg>
          brookvaleyards
        </li>
        <li class="contact__item">
          <svg class="contact__icon" viewBox="0 0 24 24" aria-hidden="true"><rect x="3" y="3" width="18" height="18" rx="2"/></svg>
          brookvaleyard
        </li>
      </ul>
    </div>
    <svg class="band" viewBox="0 0 720 28" preserveAspectRatio="none" aria-hidden="true">
      <polygon points="0,0 470,0 462,28 0,28" fill="var(--leaf-light)"/>
      <polygon points="476,0 720,0 720,28 468,28" fill="var(--leaf-dark)"/>
    </svg>
  </section>

  <section class="card card--back" aria-label="Card back">
    <div class="back-brand">
      <span class="back-brand__dot"></span>
      <span class="back-brand__name">Brookvale Yards</span>
    </div>
    <p class="services">
      <span>Lawn Care</span>
      <span class="services__sep"></span>
      <span>Property Maintenance</span>
      <span class="services__sep"></span>
      <span>Garden Services</span>
    </p>
  </section>

</main>
</body>
</html>
```